Website for Briar Hollow Gathering Church

Wordpress website design required for Briar Hollow Gathering Church. We are a family oriented church catering for age groups from school age to elderly people. The church has a wide variety of activities which it coordinates. The idea is to describe the activities on the activities page, but cross-link them to show which would be applicable to the different age groups.

We would like an inviting website which is easy to read and navigate.

Target Market(s)

Very wide audience - from school age youth to elderly people, so design and style should cater for both audiences.

Industry/Entity Type

Church

Coding

Coded - Design and coding required

Number of Pages Required

5+ page

Font styles to use
Sans Serif

Colors
0255a3
ffffff
0792cd
f78f20

Requirements
Must have
• Inviting website.
• Clear readable font.
• Space to import photos to balance text on each page.
• Need to project a dynamic and progressive feel for the church.
• Easy to navigate.
Nice to have
• Scrolling photos on pages. Ability to enter questions/ comments/prayer requests on Home page.
Should not have
• Conservative audience, so should not be too bold.

```html
<!DOCTYPE html>
<html lang="en">
<head>
<meta charset="utf-8">
<title>Briar Hollow Gathering Church</title>
<link href="https://fonts.googleapis.com/css2?family=Roboto:wght@400;500;700&family=Roboto+Condensed:wght@400;700&family=Roboto+Slab:wght@400;700&display=swap" rel="stylesheet">
<style>
:root{
  --navy:#0255a3;
  --blue:#0792cd;
  --cyan:#22b3d9;
  --orange:#f78f20;
  --white:#ffffff;
  --ink:#333333;
  --muted:#666666;
  --grey-bg:#efefef;
  --line:#cfcfcf;
  --sans:'Roboto',Arial,sans-serif;
  --cond:'Roboto Condensed','Arial Narrow',sans-serif;
  --slab:'Roboto Slab',Georgia,serif;
}
*{margin:0;padding:0;box-sizing:border-box}
html,body{width:1200px;height:3377px;overflow:hidden}
body{position:relative;background:var(--white);font-family:var(--sans);color:var(--ink)}

/* header */
.site-header{position:absolute;left:0;top:0;width:1200px;height:117px;background:var(--white)}
.brand{position:absolute;left:98px;top:62px;display:flex;align-items:center;gap:10px;font-family:var(--sans);font-size:20px;font-weight:500;color:var(--navy);white-space:nowrap}
.brand-dot{width:16px;height:16px;border-radius:50%;background:var(--navy)}
.top-social{position:absolute;top:26px;left:876px;display:flex;gap:14px;align-items:center}
.ring{width:30px;height:30px;border-radius:50%;border:1.5px solid #b9c6d6}
.login{font-size:12px;color:#555;margin-left:8px;display:flex;align-items:center;gap:5px}
.main-nav{position:absolute;top:84px;left:0;width:1200px;font-size:14px;color:#444}
.main-nav span{position:absolute;white-space:nowrap}
.main-nav .active{color:var(--blue)}
.nav-underline{position:absolute;left:512px;top:112px;width:58px;height:5px;background:var(--blue)}

/* hero */
.hero{position:absolute;left:0;top:117px;width:1200px;height:570px;background:linear-gradient(180deg,#5d7a3a 0%,#4c5a3a 25%,#a78d64 55%,#d9d2c5 80%,#6b6f64 100%)}
.hero-title{position:absolute;left:50%;top:428px;transform:translateX(-50%);height:94px;padding:0 34px;white-space:nowrap;background:rgba(40,30,20,.62);color:var(--white);font-family:var(--cond);font-size:36px;line-height:94px;text-align:center}
.hero-dots{position:absolute;top:639px;left:541px;display:flex;gap:14px}
.hero-dots i{display:block;width:17px;height:17px;border-radius:50%;border:2px solid var(--white)}
.hero-dots i.on{background:var(--blue)}
.notch{position:absolute;left:580px;top:672px}

/* welcome */
.welcome{position:absolute;left:0;top:687px;width:1200px;height:254px;background:var(--blue);color:var(--white);text-align:center}
.welcome h1{position:absolute;top:45px;width:100%;font-family:var(--sans);font-weight:500;font-size:28px;white-space:nowrap}
.welcome p{position:absolute;left:225px;top:92px;width:750px;font-size:12.5px;line-height:19px}
.btn{position:absolute;background:var(--orange);color:var(--white);font-family:var(--sans);font-size:15px;text-align:center;border-radius:3px}

/* photos */
.section-title{position:absolute;width:100%;text-align:center;font-family:var(--slab);font-size:28px;color:var(--navy)}
.section-lead{position:absolute;text-align:center;font-size:12.5px;line-height:20px;color:#666}
.photo{position:absolute;width:326px;height:232px;box-shadow:0 10px 14px -8px rgba(0,0,0,.35)}
.blessing{position:absolute;left:450px;top:1135px;width:295px;height:144px;background:rgba(7,70,160,.82);color:var(--white);text-align:center}
.blessing h3{font-family:var(--sans);font-weight:400;font-size:17px;margin-top:22px;white-space:nowrap}
.blessing p{font-size:12.5px;line-height:20px;margin:14px 20px 0}
.outline-btn{position:absolute;border:1.5px solid #9fb0c0;color:var(--navy);font-size:14px;text-align:center;background:var(--white)}

/* minister */
.minister{position:absolute;left:0;top:1722px;width:1200px;height:282px;background:linear-gradient(90deg,#3a3a3a,#5a5a56 40%,#44423e 70%,#2e2e2e)}
.minister h2{position:absolute;top:48px;width:100%;text-align:center;color:var(--white);font-family:var(--sans);font-weight:500;font-size:27px}
.minister p{position:absolute;left:160px;top:98px;width:880px;color:var(--white);font-size:13px;line-height:19px;text-align:center}

/* news */
.news-img{position:absolute;top:2146px;width:326px;height:180px}
.news-card{position:absolute;top:2342px;width:326px}
.news-card h4{font-family:var(--slab);font-weight:400;font-size:19px;color:#333}
.news-meta{margin-top:8px;font-size:11.5px;color:var(--blue)}
.news-meta b{color:#999;font-weight:400;margin:0 10px}
.news-card p{margin-top:10px;font-family:var(--slab);font-size:12.5px;line-height:18px;color:#444}
.news-card a{display:block;margin-top:12px;font-size:11.5px;color:var(--navy);font-weight:500;text-decoration:none}

/* contact */
.contact{position:absolute;left:0;top:2503px;width:1200px;height:446px;background:var(--grey-bg)}
.contact h2{position:absolute;left:99px;top:54px;font-family:var(--sans);font-weight:400;font-size:27px;color:#333}
.contact .intro{position:absolute;left:99px;top:96px;width:487px;font-size:12.5px;line-height:18px;color:#666;text-align:justify}
.contact h3{position:absolute;left:103px;top:200px;font-family:var(--sans);font-weight:400;font-size:19px;color:var(--blue)}
.office{position:absolute;left:103px;top:238px;font-size:12px;line-height:16px;color:#555}
.office div{margin-bottom:12px}
.sq-icons{position:absolute;left:101px;top:359px;display:flex;gap:23px}
.sq-icons i{display:block;width:36px;height:36px;border:1.5px solid var(--navy)}
.field{position:absolute;left:657px;width:421px;background:var(--white);border:1px solid #c9c9c9;font-size:11.5px;color:#888;padding:16px 14px}
.prayer{position:absolute;left:889px;top:2855px;width:189px;height:45px;line-height:45px;background:linear-gradient(180deg,#f9a24a,var(--orange));color:var(--white);font-size:14px;font-weight:500;text-align:center;border-radius:2px}

/* footer */
.footer{position:absolute;left:0;top:2949px;width:1200px;height:250px;background:var(--cyan);color:var(--white)}
.footer-mark{position:absolute;left:124px;top:61px;width:103px;height:103px;border-radius:50%;background:var(--white)}
.footer h5{position:absolute;top:54px;font-family:var(--slab);font-weight:400;font-size:16px;white-space:nowrap}
.times{position:absolute;left:322px;top:95px;font-family:var(--slab);font-size:12px;line-height:21px;width:200px}
.times div{display:flex;justify-content:space-between}
.times em{font-style:normal;flex:1;border-bottom:1px dotted rgba(255,255,255,.8);margin:0 4px 6px}
.newsletter p{position:absolute;left:606px;top:92px;width:220px;font-family:var(--slab);font-size:12px;line-height:19px}
.email-in{position:absolute;left:606px;top:154px;width:209px;height:34px;background:var(--white);color:#888;font-size:11.5px;padding:10px}
.subscribe{position:absolute;left:606px;top:200px;width:82px;height:26px;background:#1d1d1d;color:var(--white);font-size:10px;line-height:26px;text-align:center}
.follow p{position:absolute;left:894px;top:100px;width:200px;font-family:var(--slab);font-size:11.5px;line-height:17px}
.footer-social{position:absolute;left:891px;top:178px;display:flex;gap:11px}
.footer-social i{display:block;width:34px;height:34px;border-radius:50%;border:1.5px solid var(--white)}

/* mission */
.mission{position:absolute;left:0;top:3199px;width:1200px;height:178px;background:var(--orange);color:var(--white)}
.mission h5{position:absolute;left:101px;top:30px;font-family:var(--slab);font-weight:400;font-size:16px}
.mission p{position:absolute;left:101px;top:60px;width:800px;font-family:var(--slab);font-size:12px;line-height:20px}
.mission .cnt{position:absolute;left:1100px;top:40px;font-size:11px}
.mission hr{position:absolute;left:0;top:117px;width:1200px;border:0;border-top:1px solid rgba(255,255,255,.4)}
.mission .copy{position:absolute;top:140px;width:100%;text-align:center;font-size:11.5px}
</style>
</head>
<body>

<header class="site-header">
  <div class="brand"><span class="brand-dot"></span>Briar Hollow Gathering Church</div>
  <div class="top-social" aria-label="Social links">
    <span class="ring"></span><span class="ring"></span><span class="ring"></span><span class="ring"></span>
    <span class="login">
      <svg width="11" height="12" viewBox="0 0 11 12"><circle cx="5.5" cy="3.5" r="3" fill="#0792cd"/><path d="M0 12c0-4 2.5-5 5.5-5s5.5 1 5.5 5z" fill="#0792cd"/></svg>LOGIN</span>
  </div>
  <nav class="main-nav">
    <span class="active" style="left:522px">HOME</span>
    <span style="left:594px">AGE GROUP</span>
    <span style="left:702px">ACTIVITIES</span>
    <span style="left:806px">EVENTS CALENDAR</span>
    <span style="left:961px">ABOUT</span>
    <span style="left:1038px">CONTACT</span>
  </nav>
  <div class="nav-underline"></div>
</header>

<section class="hero" role="img" aria-label="Photo of a garden table set for a church lunch with orange flowers, fruit punch and plates"></section>
<div class="hero-title">BRIAR HOLLOW GATHERING CHURCH</div>
<div class="hero-dots"><i></i><i class="on"></i><i></i><i></i></div>
<svg class="notch" width="40" height="16" viewBox="0 0 40 16"><path d="M0 16 L20 0 L40 16Z" fill="#0792cd"/></svg>

<section class="welcome">
  <h1>WELCOME TO BRIAR HOLLOW GATHERING CHURCH</h1>
  <p>Veteran owned software consultancy providing consultants to both commercial and government customers. Our consultants have many years of industry experience providing innovative systems, products, and solutions in both systems engineering and software engineering for satellite ground system software and telecommunication software.</p>
  <div class="btn" style="left:538px;top:168px;width:126px;height:43px;line-height:43px">LEARN MORE</div>
</section>

<h2 class="section-title" style="top:976px">OUR PHOTOS</h2>
<p class="section-lead" style="left:230px;top:1014px;width:740px">Veteran owned software consultancy providing consultants to both commercial and government customers. Our consultants have many years of industry experience providing innovative systems, products, and solutions in both systems engineering</p>

<div class="photo" style="left:99px;top:1085px;background:linear-gradient(135deg,#8a3a32,#c9a48c 50%,#4a3a3a)" role="img" aria-label="Photo of church members gathered indoors"></div>
<div class="photo" style="left:435px;top:1085px;background:linear-gradient(135deg,#5a3a2a,#3a2a24)" role="img" aria-label="Photo of the church hall"></div>
<div class="photo" style="left:772px;top:1085px;background:linear-gradient(135deg,#4f6a34,#a99a7c 55%,#7a4a2a)" role="img" aria-label="Photo of members talking in the church garden"></div>
<div class="photo" style="left:99px;top:1357px;background:linear-gradient(135deg,#bfc5c9,#6a7066 50%,#c8b860)" role="img" aria-label="Photo of a shared lunch table in the hall"></div>
<div class="photo" style="left:435px;top:1357px;background:linear-gradient(135deg,#7a6a5a,#b8a890 50%,#5a4a3a)" role="img" aria-label="Photo of members serving food at a buffet"></div>
<div class="photo" style="left:772px;top:1357px;background:linear-gradient(135deg,#6a4a3a,#c7a88a 50%,#8a5a4a)" role="img" aria-label="Photo of members at a church celebration"></div>

<div class="blessing">
  <h3>BLESSINGS FROM BRIAR HOLLOW</h3>
  <p>We hold two services which are at 8 am (traditional worship service where we sing hymns) and at 10 am (family worship service).</p>
</div>

<div class="outline-btn" style="left:502px;top:1637px;width:194px;height:49px;line-height:47px">MORE PHOTO GALLERY</div>

<section class="minister" role="img" aria-label="Darkened photo of the congregation gathered in the hall">
  <h2>MINISTER'S WEEKLY</h2>
  <p>We hold two services which are at 8 am (traditional worship service where we sing hymns) and at 10 am (family worship service) where the children would head off to join the Micro Minis, Sunday Club or (Junior) Juice during the sermon. Holy Communion is generally held on the 3rd Sunday of the month. Our Minister is the Reverend Alan Pryce. Please check out our website and take a look at the various activities that our church offers.</p>
  <div class="btn" style="left:538px;top:187px;width:126px;height:41px;line-height:41px">LEARN MORE</div>
</section>

<h2 class="section-title" style="top:2028px">OUR NEWS</h2>
<p class="section-lead" style="left:225px;top:2077px;width:750px;font-family:var(--slab)">We only work in the Elm County area so we are local and know the area and market. We can finance or buy your home for cash. Our team will do any major renovations to the home or property and then make</p>

<div class="news-img" style="left:99px;background:linear-gradient(135deg,#6a5040,#c8b8a8 55%,#3a3a44)" role="img" aria-label="Photo of members chatting at a morning tea"></div>
<div class="news-img" style="left:437px;background:linear-gradient(135deg,#8a8a84,#d0ccc0 50%,#5a5a5a)" role="img" aria-label="Photo of a long dinner table in the hall"></div>
<div class="news-img" style="left:776px;background:linear-gradient(135deg,#4a6a3a,#b8b098 55%,#6a5a4a)" role="img" aria-label="Photo of members outdoors in the garden"></div>

<article class="news-card" style="left:99px">
  <h4>OUR BLOG TEXT</h4>
  <div class="news-meta">&#9632; Agu. 22, 2016<b>|</b>&#9675; 2 Comments</div>
  <p>There are many variations passages of Lorem Ipsum available, but the majority have suffered alteration.</p>
  <a href="#">LEARN MORE</a>
</article>
<article class="news-card" style="left:437px">
  <h4>OUR BLOG TEXT</h4>
  <div class="news-meta">&#9632; Agu. 22, 2016<b>|</b>&#9675; 2 Comments</div>
  <p>There are many variations passages of Lorem Ipsum available, but the majority have suffered alteration.</p>
  <a href="#">LEARN MORE</a>
</article>
<article class="news-card" style="left:776px">
  <h4>OUR BLOG TEXT</h4>
  <div class="news-meta">&#9632; Agu. 22, 2016<b>|</b>&#9675; 2 Comments</div>
  <p>There are many variations passages of Lorem Ipsum available, but the majority have suffered alteration.</p>
  <a href="#">LEARN MORE</a>
</article>

<section class="contact">
  <h2>CONTACT DETAIL</h2>
  <p class="intro">We live in a world with no boundaries when it comes to business and information. Fernlow is local for business rules and accounts but truly international when it comes to information dissemination, business network and trade. We are adding our foot prints across the globe, please check if Fernlow is already in your country.</p>
  <h3>VISIT OUR OFFICE</h3>
  <div class="office">
    <div># 13 Level, Our Street<br>Our Townsville NSW 2000 Our Country</div>
    <div>+61 900 555 0142</div>
    <div>info@briarhollowchurch.example</div>
  </div>
  <div class="sq-icons"><i></i><i></i><i></i><i></i></div>
</section>
<div class="field" style="top:2560px;height:52px">Your Email: *</div>
<div class="field" style="top:2621px;height:51px">Password*</div>
<div class="field" style="top:2681px;height:52px">Enter questions</div>
<div class="field" style="top:2742px;height:90px">Comments</div>
<div class="prayer">PRAYER REQUESTS</div>

<footer class="footer">
  <div class="footer-mark"></div>
  <h5 style="left:322px">SERVICE TIMES</h5>
  <div class="times">
    <div>Monday<em></em>8:00 - 19:00</div>
    <div>Tuesday<em></em>8:00 - 19:00</div>
    <div>Wednesday<em></em>8:00 - 19:00</div>
    <div>Thursday<em></em>8:00 - 19:00</div>
    <div>Friday<em></em>8:00 - 19:00</div>
    <div>Saturday<em></em>8:00 - 19:00</div>
  </div>
  <div class="newsletter">
    <h5 style="left:606px">NEWSLETTER</h5>
    <p>Register Your email address to get information about us</p>
  </div>
  <div class="email-in">Email Address</div>
  <div class="subscribe">SUBSCRIBE</div>
  <div class="follow">
    <h5 style="left:894px">FOLLOW US</h5>
    <p>Lorem ipsum dolor sit amet, conse ctetur adipiscing elit. Nulla in purus nibh. Donec ornare</p>
  </div>
  <div class="footer-social"><i></i><i></i><i></i><i></i><i></i></div>
</footer>

<section class="mission">
  <h5>THEME/MISSION</h5>
  <p>Since 1958, the Church has had two redevelopment phases and now closely resembles the original 1950s masterplan. Appropriately for the majestic real estate on which it is built, Church stationery and logo depicts 'Hope on the Rise.'</p>
  <span class="cnt">C 19</span>
  <hr>
  <div class="copy">© Copyright 2016 Briar Hollow Gathering Church - All Rights Reserved</div>
</section>

</body>
</html>
```